Hello my name is Colin, I am Starting a business called Lumen Wellness and fitness and am in need of a memorable business card.
It is a personal training studio. I have added the logo that i would like to be on the left center om my business card. i would like room left up the top for a heading sentence such as. "Is your body shocking for all the wrong reasons". there must be room left on the right of the logo below the main heading for 3 sub headings.
then under those 3 headings and logo room for another larger heading eg. "give me a call and learn how to eat chocolate, drink bear and have great sex". in what room is left i would like to be used for my contact details, use I'm Colin Ferrante your fitness expert on the left then on the right Phone, Email and website space in at least 12 Point. Very specific i know :) now onto the back, for the back i would like an eye catching graphic and room for one main headline and 3 bullet points centered just write anything i will choose what to put in them when i pick a winner. Thank you very much for sticking through all of that :) i appreciate you taking the time to read it and hopefully undergo designing me a business card.
I can't wait to see the designs!

Target Market(s)

slightly more towards females although it would probably be best if it was targeted towards both sexes

Industry/Entity Type

Training

Requirements
Nice to have
• I would love to see if anyone could come up with a design that would really make my card stand out and be memorable.
Should not have
• tacky fitness photos of abs and muscles etc.

```html
<!DOCTYPE html>
<html lang="en">
<head>
<meta charset="utf-8">
<title>Lumen Wellness and fitness – Business Card</title>
<link rel="stylesheet" href="https://fonts.googleapis.com/css2?family=Questrial&family=Open+Sans:wght@400;600&display=swap">
<style>
  :root {
    --stage: #8a5633;
    --card: #ffffff;
    --brand-blue: #1f4f86;
    --brand-blue-light: #2d65a3;
    --ink: #333333;
    --label-ink: #111111;
  }
  * { margin: 0; padding: 0; box-sizing: border-box; }
  html, body { width: 1200px; height: 788px; overflow: hidden; }
  body {
    background: var(--stage);
    font-family: "Questrial", "Century Gothic", sans-serif;
    color: var(--ink);
    position: relative;
  }
  .side-label {
    position: absolute;
    font-family: "Open Sans", Arial, sans-serif;
    font-size: 21px;
    color: var(--label-ink);
    transform: translateX(-50%);
    white-space: nowrap;
  }
  .card {
    position: absolute;
    width: 524px;
    height: 299px;
    background: var(--card);
    border-radius: 22px;
  }
  .card-front { left: 338px; top: 73px; }
  .card-back-one { left: 54px; top: 446px; }
  .card-back-two { left: 621px; top: 441px; }

  .centered { position: absolute; left: 0; right: 0; text-align: center; white-space: nowrap; }

  .headline-small { font-size: 13px; color: var(--ink); }
  .brand-name { color: var(--brand-blue); font-weight: 400; line-height: 1; }
  .front-brand { top: 80px; font-size: 62px; }
  .front-brand-sub { top: 140px; font-size: 17px; }
  .front-promise { top: 190px; font-size: 12.5px; color: var(--brand-blue); }
  .front-person { top: 229px; font-size: 13.5px; color: var(--brand-blue); }
  .front-person strong { font-weight: 400; color: #173e6a; }
  .front-contact { top: 270px; font-size: 13.5px; color: var(--ink); }
  .front-contact b { font-family: "Open Sans", Arial, sans-serif; font-weight: 600; font-style: italic; }

  .figure-area {
    position: absolute;
    left: 42px; top: 20px;
    width: 150px; height: 262px;
    background: linear-gradient(180deg, var(--brand-blue-light), var(--brand-blue));
    border-radius: 60px 60px 14px 14px;
  }
  .back-one-brand { position: absolute; left: 255px; top: 22px; }
  .back-one-brand .brand-name { display: block; }
  .back-one-brand .name-main { font-size: 36px; }
  .back-one-brand .name-sub { font-size: 10.5px; margin-top: 2px; }
  .bullet-list {
    position: absolute; left: 258px; top: 117px;
    list-style: none;
    font-family: "Open Sans", Arial, sans-serif;
    font-size: 16.5px; color: #111;
  }
  .bullet-list li { position: relative; padding-left: 25px; height: 33px; }
  .bullet-list li::before {
    content: ""; position: absolute; left: 0; top: 9px;
    width: 6px; height: 6px; background: #111;
  }
  .back-one-web {
    position: absolute; left: 256px; top: 253px;
    font-size: 20px; color: #3a3a3a;
  }

  .back-two-tagline { top: 20px; }
  .back-two-brand { top: 82px; font-size: 92px; }
  .back-two-brand-sub { top: 178px; font-size: 22px; }
  .back-two-web { top: 253px; font-size: 19px; letter-spacing: 4px; color: #3a3a3a; }
</style>
</head>
<body>
  <div class="side-label" style="left:600px; top:33px;">Front</div>
  <div class="side-label" style="left:323px; top:403px;">Back - 1</div>
  <div class="side-label" style="left:897px; top:403px;">Back - 2</div>

  <section class="card card-front">
    <p class="centered headline-small" style="top:21px;">Is your body shocking for all the wrong reasons</p>
    <p class="centered brand-name front-brand">Lumen</p>
    <p class="centered brand-name front-brand-sub">Wellness and fitness</p>
    <p class="centered front-promise">give me a call and learn how to eat chocolate drink bear and have great sex</p>
    <p class="centered front-person"><strong>Colin Ferrante</strong>, Fitness Expert</p>
    <p class="centered front-contact"><b>p</b> : +12 345 67890 | <b>e</b> : info@website.com | <b>w</b> : www.website.com</p>
  </section>

  <section class="card card-back-one">
    <div class="figure-area" role="img" aria-label="Blue silhouette illustration of a man and a woman standing"></div>
    <div class="back-one-brand">
      <span class="brand-name name-main">Lumen</span>
      <span class="brand-name name-sub">Wellness and fitness</span>
    </div>
    <ul class="bullet-list">
      <li>Lorem Ipsum has been ...</li>
      <li>Lorem Ipsum has been ...</li>
      <li style="margin-top:3px;">Lorem Ipsum has been ...</li>
    </ul>
    <p class="back-one-web">www.website.com</p>
  </section>

  <section class="card card-back-two">
    <p class="centered headline-small back-two-tagline">Is your body shocking for all the wrong reasons</p>
    <p class="centered brand-name back-two-brand">Lumen</p>
    <p class="centered brand-name back-two-brand-sub">Wellness and fitness</p>
    <p class="centered back-two-web">www.website.com</p>
  </section>
</body>
</html>
```